Business card for law firm

Need business card for new law firm. Think confident, authoritative, conservative, but not stuffy or old-fashioned.

Contact Information for Business Card

Content for card - logo (uploaded), plus the following:

Paul Whitcombe (larger font)
Managing Partner (larger font, but not as large as name)
Level 9, 7 Ferris Lane
Sydney NSW 2000
Main Tel 02 9364 2710
Direct Tel 02 8472 3159
Email paul@qvlegal.com.au
www.qvlegal.com.au

Letterhead design should include logo plus:
Level 9, 7 Ferris Lane
Sydney NSW 2000
Tel 02 8472 3159
www.qvlegal.com.au

```html
<!DOCTYPE html>
<html lang="en">
<head>
<meta charset="utf-8">
<title>Quayvale Legal — Business Card</title>
<link href="https://fonts.googleapis.com/css2?family=Cinzel:wght@500;600&family=Jost:wght@400&display=swap" rel="stylesheet">
<style>
  :root {
    --backdrop: #e8e8e8;
    --card-white: #ffffff;
    --navy: #0b1f5a;
    --navy-deep: #0a1d55;
    --ink: #1a1a1a;
    --grey-text: #6f6f6f;
    --address-text: #4a4a4a;
    --web-tint: #8e9ac0;
  }
  * { margin: 0; padding: 0; box-sizing: border-box; }
  html, body { width: 1125px; height: 1200px; overflow: hidden; background: var(--backdrop); }
  .canvas { position: relative; width: 1125px; height: 1200px; }

  .card { position: absolute; left: 150px; width: 825px; height: 471px; overflow: hidden; }
  .card--front { top: 98px; background: var(--card-white); }
  .card--back { top: 631px; background: var(--navy-deep); }

  .brand { position: absolute; right: 44px; top: 50px; display: flex; flex-direction: column; align-items: flex-end; }
  .brand__square { width: 62px; height: 62px; background: var(--navy); margin-right: 122px; margin-bottom: 40px; }
  .brand__name { font-family: "Cinzel", serif; font-weight: 500; font-size: 31px; letter-spacing: 0.06em; color: var(--ink); white-space: nowrap; }

  .person { position: absolute; left: 46px; top: 262px; }
  .person__name { font-family: "Cinzel", serif; font-weight: 600; font-size: 32px; color: var(--navy); letter-spacing: 0.01em; line-height: 1; }
  .person__role { font-family: "Jost", sans-serif; font-size: 20px; color: var(--grey-text); margin-top: 8px; letter-spacing: 0.01em; }

  .rule { position: absolute; left: 46px; right: 44px; top: 338px; height: 2px; background: var(--ink); }

  .contacts { position: absolute; left: 46px; top: 354px; list-style: none; font-family: "Jost", sans-serif; font-size: 21px; color: var(--grey-text); }
  .contacts li { display: flex; align-items: center; height: 27px; }
  .contacts svg { width: 20px; height: 20px; margin-right: 16px; fill: var(--navy); }

  .address { position: absolute; right: 44px; top: 354px; text-align: right; font-family: "Jost", sans-serif; font-size: 21px; color: var(--address-text); font-style: normal; }
  .address span { display: block; height: 27px; line-height: 27px; }

  .band { position: absolute; left: 0; bottom: 0; width: 825px; height: 16px; }

  .back-brand { position: absolute; left: 0; right: 0; top: 130px; display: flex; flex-direction: column; align-items: center; }
  .back-brand__square { width: 150px; height: 150px; background: var(--card-white); margin-bottom: 30px; }
  .back-brand__name { font-family: "Cinzel", serif; font-weight: 500; font-size: 30px; letter-spacing: 0.08em; color: var(--card-white); }
  .back-web { position: absolute; left: 0; right: 0; top: 404px; text-align: center; font-family: "Jost", sans-serif; font-size: 20px; letter-spacing: 0.62em; color: var(--web-tint); }
</style>
</head>
<body>
<main class="canvas">
  <section class="card card--front" aria-label="Card front">
    <div class="brand">
      <div class="brand__square"></div>
      <div class="brand__name">QUAYVALE LEGAL</div>
    </div>

    <div class="person">
      <h1 class="person__name">PAUL WHITCOMBE</h1>
      <p class="person__role">MANAGING PARTNER</p>
    </div>

    <div class="rule"></div>

    <ul class="contacts">
      <li><svg viewBox="0 0 20 20" aria-hidden="true"><path d="M2 7c0-2 3-4 8-4s8 2 8 4v1.5h-4V7c-1-.6-2.5-.9-4-.9S7 6.4 6 7v1.5H2z"/><path d="M5 10h10l1.5 7h-13z"/></svg>02 9364 2710</li>
      <li><svg viewBox="0 0 20 20" aria-hidden="true"><path d="M6 1h8a1 1 0 0 1 1 1v16a1 1 0 0 1-1 1H6a1 1 0 0 1-1-1V2a1 1 0 0 1 1-1zm1 2.5v11h6v-11zM10 15.8a1 1 0 1 0 0 2 1 1 0 0 0 0-2z"/></svg>02 8472 3159</li>
      <li><svg viewBox="0 0 20 20" aria-hidden="true"><path d="M2 6h16v1l-8 5-8-5zM2 9l8 5 8-5v6H2z"/></svg>paul@qvlegal.com.au</li>
    </ul>

    <address class="address">
      <span>Level 9, 7 Ferris Lane</span>
      <span>Sydney NSW 2000</span>
      <span>www.qvlegal.com.au</span>
    </address>

    <svg class="band" viewBox="0 0 825 16" aria-hidden="true">
      <polygon points="0,0 454,0 450,16 0,16" fill="var(--navy)"/>
      <polygon points="461,0 825,0 825,16 457,16" fill="var(--ink)"/>
    </svg>
  </section>

  <section class="card card--back" aria-label="Card back">
    <div class="back-brand">
      <div class="back-brand__square"></div>
      <div class="back-brand__name">QUAYVALE LEGAL</div>
    </div>
    <p class="back-web">www.qvlegal.com.au</p>
  </section>
</main>
</body>
</html>
```